I would like a business card to match my truck wrap and logo. I would like the font to match my existing business card please.

Industry/Entity Type

Painter

Contact Information for Business Card

Rodrigo Fenwar 801-437-2190 Fenwarcoatings.utah@brelmox.com
SERVICES - Custom Paint & Stain, Interior & Exterior, Epoxy Coatings / Garage Floors, Cabinet Refinishing, Log Staining and Refinishing.

Requirements
Nice to have
• I would like to have the white and grey line like the bottom of my vehicle wrap, Light Grey to match my truck also.

```html
<!DOCTYPE html>
<html lang="en">
<head>
<meta charset="utf-8">
<title>Fenwar Coatings Business Card</title>
<link rel="stylesheet" href="https://fonts.googleapis.com/css2?family=Roboto:wght@400;500&display=swap">
<style>
  :root {
    --bg: #2b2b2d;
    --card-dark-top: #434345;
    --card-dark-bottom: #2f2f31;
    --card-light: #ffffff;
    --brand-blue: #1a9ee6;
    --brand-blue-deep: #1177c4;
    --text-light: #f2f2f2;
    --text-dark: #444449;
    --text-muted: #5a5a60;
  }
  * { box-sizing: border-box; margin: 0; padding: 0; }
  html, body { width: 1200px; height: 930px; overflow: hidden; }
  body {
    background: var(--bg);
    font-family: "Roboto", Arial, sans-serif;
    position: relative;
  }
  .card {
    position: absolute;
    width: 620px;
    height: 354px;
    border-radius: 22px;
    overflow: hidden;
    box-shadow: 0 14px 30px rgba(0,0,0,0.45);
  }
  .card__band {
    position: absolute;
    left: 0; right: 0; bottom: 0;
    height: 12px;
    background: linear-gradient(90deg, var(--brand-blue), var(--brand-blue-deep));
  }

  /* Back of card: services */
  .card--back {
    left: 90px; top: 70px;
    background: linear-gradient(160deg, var(--card-dark-top), var(--card-dark-bottom));
  }
  .brand {
    display: flex;
    align-items: center;
    gap: 14px;
  }
  .brand__mark {
    width: 46px; height: 46px;
    background: var(--brand-blue);
    border-radius: 6px;
    flex: none;
  }
  .brand__name {
    font-weight: 500;
    font-size: 34px;
    letter-spacing: 1px;
    color: var(--brand-blue);
    text-transform: uppercase;
    white-space: nowrap;
  }
  .card--back .brand {
    position: absolute;
    left: 0; right: 0; top: 92px;
    justify-content: center;
  }
  .services {
    position: absolute;
    left: 30px; right: 30px; top: 186px;
    text-align: center;
  }
  .services__title {
    font-size: 20px;
    font-weight: 400;
    color: var(--brand-blue);
    letter-spacing: 1px;
    margin-bottom: 8px;
  }
  .services__list {
    font-size: 16px;
    line-height: 1.5;
    color: var(--text-light);
  }
  .services__sep { color: var(--brand-blue); padding: 0 4px; }

  /* Front of card: contact */
  .card--front {
    left: 490px; top: 500px;
    background: var(--card-light);
  }
  .card--front .brand {
    position: absolute;
    left: 34px; top: 160px;
    gap: 12px;
  }
  .card--front .brand__name { font-size: 22px; letter-spacing: 0.5px; }
  .card--front .brand__mark { width: 36px; height: 36px; }
  .divider {
    position: absolute;
    left: 326px; top: 110px;
    width: 2px; height: 120px;
    background: var(--brand-blue);
  }
  .contact {
    position: absolute;
    left: 344px; top: 112px;
  }
  .contact__name {
    font-size: 24px;
    font-weight: 500;
    color: var(--brand-blue);
    text-transform: uppercase;
    letter-spacing: 0.5px;
    white-space: nowrap;
  }
  .contact__role {
    font-size: 16px;
    color: var(--text-muted);
    margin-bottom: 10px;
  }
  .contact__line {
    display: flex;
    align-items: center;
    gap: 6px;
    font-size: 14px;
    color: var(--text-dark);
    line-height: 1.45;
    white-space: nowrap;
  }
  .contact__icon { width: 11px; height: 11px; flex: none; }
</style>
</head>
<body>

<section class="card card--back" aria-label="Card back with services">
  <div class="brand">
    <span class="brand__mark"></span>
    <span class="brand__name">Fenwar Coatings</span>
  </div>
  <div class="services">
    <h2 class="services__title">SERVICES</h2>
    <p class="services__list">
      Custom Paint &amp; Stain<span class="services__sep">|</span>Interior &amp; Exterior<span class="services__sep">|</span>Epoxy Coatings / Garage Floors<br>
      Cabinet Refinishing<span class="services__sep">|</span>Log Staining and Refinishing.
    </p>
  </div>
  <div class="card__band"></div>
</section>

<section class="card card--front" aria-label="Card front with contact details">
  <div class="brand">
    <span class="brand__mark"></span>
    <span class="brand__name">Fenwar Coatings</span>
  </div>
  <div class="divider"></div>
  <div class="contact">
    <h1 class="contact__name">Rodrigo Fenwar</h1>
    <p class="contact__role">Director</p>
    <p class="contact__line">
      <svg class="contact__icon" viewBox="0 0 12 12"><path d="M3 1 L5 3.5 L4 5 Q5 7 7 8 L8.5 7 L11 9 L10 11 Q4 11 1 3 Z" fill="#1a9ee6"/></svg>
      801-437-2190
    </p>
    <p class="contact__line">
      <svg class="contact__icon" viewBox="0 0 12 12"><rect x="1" y="2.5" width="10" height="7" fill="none" stroke="#1a9ee6" stroke-width="1.4"/><path d="M1 2.5 L6 7 L11 2.5" fill="none" stroke="#1a9ee6" stroke-width="1.4"/></svg>
      Fenwarcoatings.utah@brelmox.com
    </p>
    <p class="contact__line">
      <svg class="contact__icon" viewBox="0 0 12 12"><circle cx="6" cy="6" r="5" fill="none" stroke="#1a9ee6" stroke-width="1.3"/><path d="M1 6 H11 M6 1 Q3 6 6 11 M6 1 Q9 6 6 11" fill="none" stroke="#1a9ee6" stroke-width="1"/></svg>
      www.fenwarcoatings-utah.com
    </p>
  </div>
  <div class="card__band"></div>
</section>

</body>
</html>
```